External Window Signage Design – Antiaging Center

I would like to dress our shop windows in order to promote our activities in medical aesthetics, meso-aesthetics, anti-ageing care and classical beauty. In fact, our 350 m² center is located on the first floor of a building where there is a lot of traffic, as well as a bus stop and metro station. And right in front of a twenty-floor building of the Northern Trade Council.
We want to communicate our activities to our customers with photos and text in a storefront window. So that they can what we do and visit our website www.lumavera.be (our site is in French) as well as our social networks, like pictoloop, friendwall,…
We'd like a window signage : Elegant, Modern, New, Pure, Clean
We are located on the corners of a building, where we have 8 windows on one side and 10 windows on the other, the dimensions are :
Windows
• Height: 125 cm
• Width: 130 cm
Small windows
• Height: 134 cm
• Width: 40 cm
I would say let your imagination go free. I will have other projects for the winner.
Don't hesitate to ask me if you need other formats of the logo or color, like white.
Updates

https://www.craftpoolix.com/design/48261937, I'D LIKE TO HAVE A PROJECT LIKE THIS IF POSSIBLE WITH THE LITTLE WINDOW UNDERNEATH AS WELL.

Target Market(s)

People who want to take care of their external appearance, look beautiful and good looking, womens/girls - mens/boys

Requirements
Must have
• Face and silhouette of a woman. Elegant
Serious, Modern, Professional, Feminine,Upmarket
Nice to have
• To put the different treatments that we propose,
Should not have
• We absolutely don't want a classic beauty center signage, which is reviewed many times

```html
<!DOCTYPE html>
<html lang="en">
<head>
<meta charset="UTF-8">
<title>Lumavera – Window Signage</title>
<link rel="stylesheet" href="https://fonts.googleapis.com/css2?family=Great+Vibes&family=Open+Sans:wght@700&display=swap">
<style>
  :root {
    --backdrop: #b3a79c;
    --backdrop-light: #c9bfb5;
    --gold: #d6b260;
    --gold-deep: #b8924a;
    --gold-shadow: rgba(80, 60, 30, 0.35);
    --white: #ffffff;
  }
  * { margin: 0; padding: 0; box-sizing: border-box; }
  html, body { width: 1200px; height: 857px; overflow: hidden; }
  body { background: var(--backdrop); }

  .window-decal {
    position: relative;
    width: 1200px;
    height: 857px;
    background: radial-gradient(ellipse at 45% 45%, var(--backdrop-light) 0%, var(--backdrop) 70%);
    overflow: hidden;
  }

  .brand {
    position: absolute;
    left: 271px;
    top: 60px;
    display: flex;
    align-items: center;
    gap: 10px;
  }
  .brand-dot {
    width: 16px;
    height: 16px;
    border-radius: 50%;
    background: var(--gold);
  }
  .brand-name {
    font-family: "Open Sans", sans-serif;
    font-weight: 700;
    font-size: 38px;
    color: var(--white);
    letter-spacing: -0.5px;
  }

  .slogan {
    position: absolute;
    font-family: "Great Vibes", cursive;
    color: var(--gold);
    text-shadow: 3px 4px 3px var(--gold-shadow);
    line-height: 1;
    white-space: nowrap;
  }
  .slogan-make  { left: 300px; top: 215px; font-size: 190px; }
  .slogan-youth { left: 268px; top: 372px; font-size: 190px; }
  .slogan-last  { left: 345px; top: 520px; font-size: 175px; }

  .silhouette {
    position: absolute;
    left: 718px;
    top: 45px;
    width: 237px;
    height: 741px;
  }

  .website {
    position: absolute;
    left: 272px;
    top: 782px;
    font-family: "Open Sans", sans-serif;
    font-weight: 700;
    font-size: 34px;
    color: var(--white);
    letter-spacing: 1.5px;
    transform: rotate(-5deg);
    transform-origin: left center;
  }
</style>
</head>
<body>
  <main class="window-decal">
    <div class="brand">
      <span class="brand-dot"></span>
      <span class="brand-name">Lumavera</span>
    </div>

    <h1 class="slogan-block">
      <span class="slogan slogan-make">Make</span>
      <span class="slogan slogan-youth">Youth</span>
      <span class="slogan slogan-last">last</span>
    </h1>

    <svg class="silhouette" viewBox="0 0 237 741" role="img" aria-label="Gold line drawing of a standing woman's silhouette seen from behind">
      <defs>
        <linearGradient id="silhouette-fill" x1="0" y1="0" x2="0" y2="1">
          <stop offset="0" stop-color="#d6b260" stop-opacity="0.35"/>
          <stop offset="1" stop-color="#b8924a" stop-opacity="0.2"/>
        </linearGradient>
      </defs>
      <rect x="0" y="0" width="237" height="741" rx="30" fill="url(#silhouette-fill)"/>
    </svg>

    <p class="website">www.lumavera.be</p>
  </main>
</body>
</html>
```